Road Construction Company needs business cards

We would like a new business card designed for our business.

We're a road construction company based in Qld, Australia.

Can the business card please have the following information on it.

Name: Warren Halbeck
Position: General Manager
Phone: 0472 915 348
Email: warren.halbeck@tovrin.com.au
Address: 87 Marrow Ave, Pendlebay, QLD, 4023
Website: www.tovrin.com.au

Visually we'd like the card to be professional and simple.

Attached is our logo.

Our website is www.tovrin.com.au

Target Market(s)

Men aged 25-60

Contact Information for Business Card

As listed in project description

Font styles to use
Serif

Requirements
Must have
• Large logo on back of card

```html
<!DOCTYPE html>
<html lang="en">
<head>
<meta charset="utf-8">
<title>Tovrin business card</title>
<link rel="stylesheet" href="https://fonts.googleapis.com/css2?family=Poppins:wght@400;500;600;700&display=swap">
<style>
  :root {
    --stage: #949494;
    --card-dark: #221f20;
    --card-dark-edge: #1a1718;
    --card-light: #fbfbfb;
    --brand-navy: #0d4f9c;
    --brand-sky: #3aa7d9;
    --text-grey: #6b6b6b;
  }
  * { margin: 0; padding: 0; box-sizing: border-box; }
  html, body { width: 1200px; height: 1000px; overflow: hidden; }
  body {
    background: var(--stage);
    position: relative;
    font-family: "Poppins", sans-serif;
  }
  .card {
    position: absolute;
    top: 193px;
    width: 351px;
    height: 615px;
    border-radius: 28px;
    overflow: hidden;
  }
  .card-back { left: 247px; background: var(--card-dark); }
  .back-texture {
    position: absolute; inset: 0;
    background: radial-gradient(ellipse at 50% 40%, #2a2627 0%, var(--card-dark) 60%, var(--card-dark-edge) 100%);
  }
  .back-mark {
    position: absolute;
    right: 64px; bottom: 66px;
    font-size: 13px; font-weight: 700;
    color: var(--brand-sky);
    letter-spacing: 1px;
  }
  .card-front {
    left: 657px;
    background: var(--card-light);
    text-align: center;
  }
  .wordmark {
    position: absolute;
    top: 146px; left: 0; right: 0;
    font-size: 44px; font-weight: 700;
    color: var(--brand-navy);
    letter-spacing: 2px;
    line-height: 1;
  }
  .person-name {
    position: absolute; top: 302px; left: 0; right: 0;
    font-size: 20px; font-weight: 600;
    color: var(--brand-navy);
    letter-spacing: 1.2px;
  }
  .person-role {
    position: absolute; top: 328px; left: 0; right: 0;
    font-size: 14px; font-weight: 400;
    color: var(--brand-sky);
    letter-spacing: 1.4px;
  }
  .address {
    position: absolute; top: 362px; left: 0; right: 0;
    font-size: 17px; line-height: 22px;
    color: var(--text-grey);
  }
  .contact-icons {
    position: absolute; top: 426px; left: 0; right: 0;
    display: flex; justify-content: center; gap: 8px;
  }
  .contact-icon {
    width: 38px; height: 38px; border-radius: 50%;
    background: var(--brand-sky);
    display: flex; align-items: center; justify-content: center;
  }
  .contact-lines {
    position: absolute; top: 484px; left: 0; right: 0;
    font-size: 17px; line-height: 26px;
    color: var(--text-grey);
  }
</style>
</head>
<body>
  <section class="card card-back">
    <div class="back-texture" role="img" aria-label="Dark card back with a faint repeating embossed brand pattern"></div>
    <span class="back-mark">TOVRIN</span>
  </section>

  <section class="card card-front">
    <div class="wordmark">TOVRIN</div>
    <h1 class="person-name">WARREN HALBECK</h1>
    <p class="person-role">GENERAL MANAGER</p>
    <p class="address">87 Marrow Ave,<br>Pendlebay, QLD, 4023</p>
    <div class="contact-icons">
      <span class="contact-icon" aria-label="Phone">
        <svg width="18" height="18" viewBox="0 0 24 24"><path fill="#fff" d="M6.6 10.8a15 15 0 0 0 6.6 6.6l2.2-2.2a1 1 0 0 1 1-.25 11.4 11.4 0 0 0 3.6.57 1 1 0 0 1 1 1V20a1 1 0 0 1-1 1A17 17 0 0 1 3 4a1 1 0 0 1 1-1h3.5a1 1 0 0 1 1 1c0 1.25.2 2.45.57 3.6a1 1 0 0 1-.25 1z"/></svg>
      </span>
      <span class="contact-icon" aria-label="Email">
        <svg width="20" height="16" viewBox="0 0 20 16"><rect x="1" y="2" width="18" height="12" fill="none" stroke="#fff" stroke-width="1.6"/><path d="M1 2l9 7 9-7" fill="none" stroke="#fff" stroke-width="1.6"/></svg>
      </span>
      <span class="contact-icon" aria-label="Website">
        <svg width="20" height="20" viewBox="0 0 20 20" fill="none" stroke="#fff" stroke-width="1.4"><circle cx="10" cy="10" r="8"/><ellipse cx="10" cy="10" rx="3.5" ry="8"/><path d="M2 10h16M3.2 6h13.6M3.2 14h13.6"/></svg>
      </span>
    </div>
    <p class="contact-lines">0472 915 348<br>warren.halbeck@tovrin.com.au<br>tovrin.com.au</p>
  </section>
</body>
</html>
```